Harbourline Electrical Solutions

On one side. LOGO (underneath:) Commercial Industrial Residential

- NAME & CONTACT DETAILS

Marcus T. Hollings
Project Manager

(Cell icon) (441) 555-0187
(Email icon) hlelectricalsolutions@mailvento.com
(Facebook & Instagram icons )@hlelectricalsolutions

Other side: LOGO - underneath ELECTRICAL CONSTRUCTION & MAINTENANCE . LED LIGHTING & AUTOMATION . LIFE SAFETY SYSTEMS (FIRE ALARM / SECURITY) . DATA & COMMUNICATION

```html
<!DOCTYPE html>
<html lang="en">
<head>
<meta charset="utf-8">
<title>Harbourline Electrical Solutions – Business Card</title>
<link rel="stylesheet" href="https://fonts.googleapis.com/css2?family=Montserrat:wght@500;600&family=Roboto:wght@400;500&family=Saira+Semi+Condensed:wght@600&display=swap">
<style>
  :root {
    --backdrop: #3b3b3c;
    --card: #1e1e1f;
    --ink: #f2f2f2;
    --ink-soft: #d9d9d9;
    --silver: #8a8a8c;
    --accent: #1a86c9;
    --accent-deep: #1f6f96;
  }
  * { box-sizing: border-box; margin: 0; padding: 0; }
  html, body { width: 799px; height: 1200px; overflow: hidden; }
  body {
    background: var(--backdrop);
    font-family: "Roboto", Arial, sans-serif;
    position: relative;
  }
  .card {
    position: absolute;
    left: 60px;
    width: 680px;
    height: 390px;
    background: var(--card);
    border-radius: 4px;
    box-shadow: 0 10px 30px rgba(0,0,0,.35);
    overflow: hidden;
  }
  .card--services { top: 140px; }
  .card--contact { top: 670px; }

  /* wordmark */
  .wordmark {
    position: absolute;
    font-family: "Montserrat", Arial, sans-serif;
    font-weight: 600;
    text-transform: uppercase;
    letter-spacing: 4px;
    line-height: 1.08;
  }
  .card--services .wordmark {
    top: 62px; right: 70px;
    font-size: 30px;
    color: var(--silver);
    text-align: left;
  }
  .card--contact .wordmark {
    top: 48px; left: 60px;
    font-size: 30px;
    color: var(--ink);
  }
  .wordmark-square {
    position: absolute;
    top: 56px; left: 26px;
    width: 22px; height: 22px;
    background: var(--accent-deep);
  }

  .rule {
    position: absolute;
    height: 2px;
    background: var(--accent);
  }
  .card--services .rule { left: 60px; right: 60px; top: 210px; }
  .card--contact .rule { left: 300px; right: 50px; top: 268px; background: var(--accent-deep); }

  .services {
    position: absolute;
    left: 60px; right: 60px; top: 222px;
    color: var(--ink);
    font-size: 17px;
    line-height: 1.45;
  }
  .sectors {
    position: absolute;
    font-family: "Montserrat", Arial, sans-serif;
    font-weight: 500;
    letter-spacing: 2.5px;
    color: var(--ink);
    text-transform: uppercase;
  }
  .card--services .sectors { left: 60px; top: 300px; font-size: 17px; }
  .card--contact .sectors { left: 62px; top: 170px; font-size: 14px; color: var(--ink-soft); }
  .sectors .sep { margin: 0 14px; }

  .person {
    position: absolute;
    left: 60px; top: 216px;
  }
  .person-name {
    font-family: "Saira Semi Condensed", Arial, sans-serif;
    font-weight: 600;
    font-style: italic;
    font-size: 26px;
    color: var(--accent-deep);
    line-height: 1.05;
  }
  .person-role { font-size: 17px; color: var(--ink); margin-top: 2px; }

  .contacts {
    position: absolute;
    left: 36px; top: 290px;
    list-style: none;
    color: var(--ink);
    font-size: 17px;
    line-height: 1.6;
  }
  .contacts li { display: flex; align-items: center; gap: 8px; }
  .contacts svg { width: 16px; height: 16px; flex: none; }

  .social {
    position: absolute;
    right: 50px; bottom: 36px;
    display: flex; align-items: center; gap: 10px;
    color: var(--ink);
    font-size: 18px;
  }
  .social-dot {
    width: 16px; height: 16px;
    border: 2px solid var(--accent-deep);
    border-radius: 50%;
  }
</style>
</head>
<body>

<section class="card card--services" aria-label="Services side">
  <div class="wordmark">Harbourline<br>Electrical<br>Solutions</div>
  <div class="rule"></div>
  <p class="services">
    Electrical Construction &amp; Maintenance | Led Lighting &amp; Automation<br>
    Life Safety Systems (Fire Alarm/Security) | Data &amp; Communication
  </p>
  <p class="sectors">Commercial<span class="sep">|</span>Industrial<span class="sep">|</span>Residential</p>
</section>

<section class="card card--contact" aria-label="Contact side">
  <div class="wordmark-square"></div>
  <div class="wordmark">Harbourline<br>Electrical<br>Solutions</div>
  <p class="sectors">Commercial<span class="sep">|</span>Industrial<span class="sep">|</span>Residential</p>

  <div class="person">
    <p class="person-name">Marcus T. Hollings</p>
    <p class="person-role">Project Manager</p>
  </div>
  <div class="rule"></div>

  <ul class="contacts">
    <li>
      <svg viewBox="0 0 16 16" aria-hidden="true"><path d="M3 2h3l1.5 3.5-2 1.2a8 8 0 0 0 3.8 3.8l1.2-2L14 10v3a1.5 1.5 0 0 1-1.5 1.5A11 11 0 0 1 1.5 3.5 1.5 1.5 0 0 1 3 2z" fill="#1f6f96"/></svg>
      (441) 555-0187
    </li>
    <li>
      <svg viewBox="0 0 16 16" aria-hidden="true"><rect x="1" y="3" width="14" height="10" rx="1" fill="none" stroke="#1f6f96" stroke-width="1.6"/><path d="M1.5 3.8 8 9l6.5-5.2" fill="none" stroke="#1f6f96" stroke-width="1.6"/></svg>
      hlelectricalsolutions@mailvento.com
    </li>
  </ul>

  <div class="social">
    <span class="social-dot" aria-hidden="true"></span>
    @hlelectricalsolutions
  </div>
</section>

</body>
</html>
```